Real Estate Media Company Business Card

’m looking for a modern, high-end, double-sided business card for:
Bright Harbor Studios LLC
(Real Estate Photography & Videography)
The design should feel clean, minimal, and premium, appealing to top real estate agents and brokers.
👉 Horizontal layout is preferred
👉 Vertical option is welcome but not required
⸻
Front Side (Main Information):
Include:
* Desmond Whitfield
* Bright Harbor Studios LLC
* Title (open to creative improvement)
* Phone Number
* Email
* Website
⸻
Services Section (VERY IMPORTANT):
This should be a key visual element, not an afterthought.
Services to Include:
* Cinematic Video
* Real Estate Photography
* Drone
* Social Media Reels
* Floor Plans
* Use clean, modern icons next to each service
* Icons should be simple, minimal, and consistent style (outline or thin line preferred)
* Option to place icons inside small circles (like reference)
Layout:
* Format services similar to a clean horizontal or grid-style list (like “example 2”)
* Keep spacing balanced and uncluttered
* Make this section visually appealing and easy to scan
⸻
Back Side:
* Keep it extremely minimal
* Only include the logo in a corner
* No additional text needed
⸻
Typography & Style:
* Modern, clean, slightly bold fonts (based on uploaded references)
* Strong hierarchy (name + services stand out most)
* Plenty of white/negative space
* Avoid clutter
⸻
Overall Feel:
* Luxury
* Modern
* Clean
* Confident
* High-end real estate branding
⸻
Notes for Designers:
* Simplicity is key
* Services section should feel polished and intentional
* This card should feel like something a top-producing real estate agent would keep
Target Market(s)
Real estate agent agents

```html
<!DOCTYPE html>
<html lang="en">
<head>
<meta charset="utf-8">
<title>Bright Harbor Studios – Business Card</title>
<link rel="stylesheet" href="https://fonts.googleapis.com/css2?family=Ubuntu:wght@400;500&display=swap">
<style>
  :root {
    --backdrop: #4a3b2c;
    --card-black: #121212;
    --ink-white: #f4f4f4;
    --rule-white: #e8e8e8;
    --steel-light: #9c9a9c;
    --steel-dark: #6f6d70;
  }
  * { box-sizing: border-box; margin: 0; padding: 0; }
  html, body { width: 1060px; height: 1200px; overflow: hidden; }
  body {
    background: var(--backdrop);
    font-family: "Ubuntu", sans-serif;
    color: var(--ink-white);
    position: relative;
  }
  .card {
    position: absolute;
    left: 160px;
    width: 740px;
    height: 422px;
    background: var(--card-black);
    box-shadow: 0 6px 18px rgba(0,0,0,0.45);
    overflow: hidden;
  }
  .card--front { top: 109px; }
  .card--back { top: 618px; }

  .identity { position: absolute; left: 37px; top: 32px; }
  .identity__name { font-size: 37px; font-weight: 500; line-height: 1.2; }
  .identity__title { font-size: 24px; font-weight: 400; line-height: 1.3; margin-top: 2px; }
  .identity__company { font-size: 27px; font-weight: 500; line-height: 1.3; margin-top: 4px; }

  .services__rule {
    position: absolute; left: 356px; top: 157px;
    width: 3px; height: 159px; background: var(--rule-white);
  }
  .services { position: absolute; left: 382px; top: 153px; list-style: none; }
  .services__item {
    display: flex; align-items: center; height: 35px;
    font-size: 23px; letter-spacing: 0.3px;
  }
  .services__icon { width: 34px; height: 22px; margin-right: 13px; flex: none; }

  .contact { position: absolute; left: 37px; top: 309px; list-style: none; }
  .contact__item {
    display: flex; align-items: center; height: 31.5px;
    font-size: 20px; letter-spacing: 0.4px;
  }
  .contact__icon { width: 24px; height: 24px; margin-right: 12px; flex: none; }

  .back__texture {
    position: absolute; left: 0; top: 0; width: 100%; height: 253px;
    background: linear-gradient(160deg, var(--steel-light) 0%, #8b898c 45%, var(--steel-dark) 100%);
  }
  .back__brand {
    position: absolute; left: 451px; top: 290px; width: 242px;
    text-align: center; font-size: 21px; font-weight: 400;
    letter-spacing: 2px; color: var(--ink-white);
  }
</style>
</head>
<body>
  <section class="card card--front">
    <div class="identity">
      <h1 class="identity__name">Desmond Whitfield</h1>
      <p class="identity__title">Founder | Real Estate Media Specialist</p>
      <p class="identity__company">Bright Harbor Studios LLC</p>
    </div>

    <div class="services__rule"></div>
    <ul class="services">
      <li class="services__item"><svg class="services__icon" viewBox="0 0 34 22" fill="none" stroke="#f4f4f4" stroke-width="1.2"><rect x="1" y="4" width="32" height="17" rx="1.5"/><path d="M11 4 L13 1 H21 L23 4"/><circle cx="17" cy="12.5" r="6"/><circle cx="17" cy="12.5" r="3.5"/><rect x="3" y="2" width="4" height="2"/></svg>Cinematic Video</li>
      <li class="services__item"><svg class="services__icon" viewBox="0 0 34 22" fill="none" stroke="#f4f4f4" stroke-width="1.2"><rect x="1" y="4" width="32" height="17" rx="1.5"/><path d="M11 4 L13 1 H21 L23 4"/><circle cx="17" cy="12.5" r="6"/><circle cx="17" cy="12.5" r="3.5"/><rect x="3" y="2" width="4" height="2"/></svg>Real Estate Photography</li>
      <li class="services__item"><svg class="services__icon" viewBox="0 0 34 22" fill="none" stroke="#f4f4f4" stroke-width="1.2"><rect x="1" y="4" width="32" height="17" rx="1.5"/><path d="M11 4 L13 1 H21 L23 4"/><circle cx="17" cy="12.5" r="6"/><circle cx="17" cy="12.5" r="3.5"/><rect x="3" y="2" width="4" height="2"/></svg>Drone</li>
      <li class="services__item"><svg class="services__icon" viewBox="0 0 34 22" fill="none" stroke="#f4f4f4" stroke-width="1.2"><rect x="1" y="4" width="32" height="17" rx="1.5"/><path d="M11 4 L13 1 H21 L23 4"/><circle cx="17" cy="12.5" r="6"/><circle cx="17" cy="12.5" r="3.5"/><rect x="3" y="2" width="4" height="2"/></svg>Social Media Reels</li>
      <li class="services__item"><svg class="services__icon" viewBox="0 0 34 22" fill="none" stroke="#f4f4f4" stroke-width="1.2"><rect x="1" y="4" width="32" height="17" rx="1.5"/><path d="M11 4 L13 1 H21 L23 4"/><circle cx="17" cy="12.5" r="6"/><circle cx="17" cy="12.5" r="3.5"/><rect x="3" y="2" width="4" height="2"/></svg>Floor Plans</li>
    </ul>

    <ul class="contact">
      <li class="contact__item"><svg class="contact__icon" viewBox="0 0 24 24" fill="#f4f4f4"><path d="M6.6 10.8a15.1 15.1 0 0 0 6.6 6.6l2.2-2.2a1 1 0 0 1 1-.25 11.4 11.4 0 0 0 3.6.57 1 1 0 0 1 1 1V20a1 1 0 0 1-1 1A17 17 0 0 1 3 4a1 1 0 0 1 1-1h3.5a1 1 0 0 1 1 1c0 1.25.2 2.45.57 3.57a1 1 0 0 1-.25 1z"/></svg>610-555-0147</li>
      <li class="contact__item"><svg class="contact__icon" viewBox="0 0 24 24" fill="#f4f4f4"><path d="M2 5h20v14H2z M3.5 6.5 12 12.5l8.5-6z" fill-rule="evenodd"/></svg>desmond@brightharborstudios.com</li>
      <li class="contact__item"><svg class="contact__icon" viewBox="0 0 24 24" fill="none" stroke="#f4f4f4" stroke-width="1.5"><circle cx="12" cy="12" r="10"/><ellipse cx="12" cy="12" rx="4.5" ry="10"/><path d="M2 12h20M4 7h16M4 17h16"/></svg>www.brightharborstudios.com</li>
    </ul>
  </section>

  <section class="card card--back">
    <div class="back__texture" role="img" aria-label="Brushed grey metallic texture"></div>
    <p class="back__brand">BRIGHT HARBOR</p>
  </section>
</body>
</html>
```